Construction Company

Design a clutter free business card, it can be double-sided utilizing the logo for VKM Ltd simple with all relevant contact information.

Please also a letterhead design to function for the purposes of invoicing, all mail requirements, with header to be distinctive while the footer ties page together and incorporates all necessary information.

For now, please use generic / dummy text and when a winner is selected, I will disclose the contact information.

Hi Designers! Please read the updated brief which includes the design of a business card and letterhead. Thank you!

```html
<!DOCTYPE html>
<html lang="en">
<head>
<meta charset="utf-8">
<title>VKM Ltd — Business Card</title>
<link href="https://fonts.googleapis.com/css2?family=Roboto:wght@400;500;700&display=swap" rel="stylesheet">
<style>
  :root {
    --brand-blue: #00308f;
    --brand-blue-light: #1d63f2;
    --brand-gold: #b38a05;
    --text-grey: #555555;
    --card-white: #ffffff;
    --stage: #8c8c8c;
  }
  * { margin: 0; padding: 0; box-sizing: border-box; }
  html, body { width: 1200px; height: 1200px; overflow: hidden; }
  body {
    background: var(--stage);
    font-family: 'Roboto', sans-serif;
    position: relative;
  }
  .card {
    position: absolute;
    left: 262px;
    width: 686px;
    height: 392px;
    border-radius: 26px;
    overflow: hidden;
  }
  .card--front { top: 165px; background: var(--card-white); }
  .card--back { top: 653px; background: var(--brand-blue); }

  .brand-name {
    position: absolute;
    left: 93px;
    top: 178px;
    display: flex;
    align-items: center;
    gap: 12px;
    font-weight: 700;
    font-size: 50px;
    line-height: 1;
    color: var(--brand-blue);
    white-space: nowrap;
  }
  .brand-dot {
    width: 18px; height: 18px;
    border-radius: 50%;
    background: var(--brand-gold);
  }
  .divider {
    position: absolute;
    left: 387px; top: 93px;
    width: 1px; height: 186px;
    background: #777;
  }
  .contact {
    position: absolute;
    left: 415px; top: 90px;
    color: var(--text-grey);
  }
  .contact__name {
    font-size: 24px; font-weight: 500;
    color: var(--brand-blue);
    line-height: 1.1;
  }
  .contact__title {
    font-size: 15.5px; font-weight: 500;
    color: var(--brand-gold);
    margin-top: 1px;
  }
  .contact__address {
    font-size: 15.5px; line-height: 19px;
    margin-top: 14px;
  }
  .contact__list { list-style: none; margin-top: 13px; }
  .contact__list li {
    display: flex; align-items: center; gap: 9px;
    font-size: 15.5px; line-height: 19.5px;
  }
  .contact__list svg { width: 13px; height: 13px; fill: var(--brand-blue); flex: none; }

  .web-band {
    position: absolute;
    left: 0; top: 331px;
    width: 100%; height: 31px;
    display: flex;
  }
  .web-band__blue {
    width: 483px;
    background: var(--brand-blue);
    color: #fff;
    font-size: 15px;
    letter-spacing: 6.5px;
    line-height: 31px;
    padding-left: 116px;
  }
  .web-band__gold { flex: 1; background: var(--brand-gold); }

  .back-brand {
    position: absolute;
    left: 0; right: 0; top: 138px;
    text-align: center;
    font-weight: 700;
    font-size: 104px;
    line-height: 1;
    color: var(--brand-blue-light);
  }
</style>
</head>
<body>
  <section class="card card--front" aria-label="Business card front">
    <div class="brand-name"><span>VKM Ltd</span><span class="brand-dot"></span></div>
    <div class="divider"></div>
    <div class="contact">
      <p class="contact__name">DANIEL REYES</p>
      <p class="contact__title">President</p>
      <p class="contact__address">2140 Cedar Ridge Road<br>Fairbanks, Alaska 99701</p>
      <ul class="contact__list">
        <li><svg viewBox="0 0 24 24"><path d="M6.6 10.8a15 15 0 0 0 6.6 6.6l2.2-2.2c.3-.3.7-.4 1-.2 1.1.4 2.3.6 3.6.6.6 0 1 .4 1 1V20c0 .6-.4 1-1 1A17 17 0 0 1 3 4c0-.6.4-1 1-1h3.5c.6 0 1 .4 1 1 0 1.3.2 2.5.6 3.6.1.3 0 .7-.2 1z"/></svg>555-214-7730</li>
        <li><svg viewBox="0 0 24 24"><path d="M7 1h10a2 2 0 0 1 2 2v18a2 2 0 0 1-2 2H7a2 2 0 0 1-2-2V3a2 2 0 0 1 2-2zm0 3v14h10V4z"/></svg>555-618-2094</li>
        <li><svg viewBox="0 0 24 24"><path d="M6 2h9l3 3v5H6zM3 11h18a1 1 0 0 1 1 1v7H2v-7a1 1 0 0 1 1-1zm2 10h14v2H5z"/></svg>555-342-1186</li>
        <li><svg viewBox="0 0 24 24"><path d="M2 5h20v14H2zm2 2v.5l8 5.5 8-5.5V7zm0 3v7h16v-7l-8 5.5z"/></svg>info@vkmltd.com</li>
      </ul>
    </div>
    <div class="web-band">
      <div class="web-band__blue">www.vkmltd.com</div>
      <div class="web-band__gold"></div>
    </div>
  </section>

  <section class="card card--back" aria-label="Business card back">
    <p class="back-brand">VKM Ltd</p>
  </section>
</body>
</html>
```